Modern Business Card

Modern professional business card with more than just logo and demographic info. Something memorable.

We are a trendy/modern chiropractic group with an emphasis on neurology, hence the minimalist-type brain logo. We want to convey that modern and technical aspect with professionalism and the elite nature of our practice environment.

```html
<!DOCTYPE html>
<html lang="en">
<head>
<meta charset="utf-8">
<title>Stature Chiropractic – Business Card</title>
<link rel="stylesheet" href="https://fonts.googleapis.com/css2?family=Quattrocento:wght@400&family=Lora:wght@400&family=Exo+2:wght@600&family=Roboto:wght@400&display=swap">
<style>
  :root {
    --backdrop: #bdbdbd;
    --card: #f3f3f3;
    --brand-blue: #3e64a0;
    --ink-dark: #3b3034;
    --ink-text: #4a4a4a;
    --white: #ffffff;
    --shadow: rgba(0, 0, 0, 0.28);
  }
  * { margin: 0; padding: 0; box-sizing: border-box; }
  html, body {
    width: 1200px; height: 576px; overflow: hidden;
    background: var(--backdrop);
  }
  .stage { position: relative; width: 1200px; height: 576px; }
  .card {
    position: absolute; top: 138px;
    width: 484px; height: 294px;
    background: var(--card);
    border-radius: 10px;
    overflow: hidden;
    box-shadow: 2px 4px 8px var(--shadow);
  }
  .card--front { left: 82px; }
  .card--back { left: 634px; }

  /* Front */
  .front-brand {
    position: absolute; left: 0; right: 0; top: 96px;
    display: flex; align-items: center; justify-content: center; gap: 16px;
  }
  .brand-mark {
    width: 26px; height: 26px; background: var(--brand-blue);
  }
  .brand-name {
    font-family: "Quattrocento", serif;
    font-weight: 400;
    color: var(--ink-dark);
    letter-spacing: 1px;
  }
  .front-brand .brand-name { font-size: 34px; line-height: 1.05; }
  .front-web {
    position: absolute; left: 0; right: 0; top: 247px;
    display: flex; align-items: center; justify-content: center; gap: 18px;
    font-family: "Roboto", sans-serif; font-size: 12.5px; color: #1e1e1e;
  }
  .front-web .dash { width: 34px; height: 2px; background: var(--brand-blue); border-radius: 2px; }
  .front-stripe {
    position: absolute; left: 0; bottom: 0; width: 100%; height: 13px;
    display: flex;
  }
  .front-stripe .blue { flex: 1; background: var(--brand-blue); }
  .front-stripe .dark { flex: 1; background: var(--ink-dark); }

  /* Back */
  .back-brand {
    position: absolute; left: 27px; top: 27px;
    display: flex; align-items: center; gap: 10px;
  }
  .back-brand .brand-mark { width: 20px; height: 20px; }
  .back-brand .brand-name { font-size: 24px; }
  .contact-band {
    position: absolute; left: 0; top: 88px; width: 100%; height: 151px;
    background: var(--brand-blue); color: var(--white);
  }
  .person-name {
    position: absolute; left: 27px; top: 20px;
    font-family: "Exo 2", sans-serif; font-weight: 600; font-size: 18px;
  }
  .person-role {
    position: absolute; left: 27px; top: 46px;
    font-family: "Lora", serif; font-size: 12px; opacity: 0.92;
  }
  .contact-list {
    position: absolute; left: 27px; top: 78px; list-style: none;
    font-family: "Lora", serif; font-size: 12px;
  }
  .contact-list li { display: flex; align-items: center; gap: 10px; height: 18.5px; }
  .contact-list svg { width: 11px; height: 11px; fill: var(--white); flex: none; }
  .address {
    position: absolute; left: 27px; top: 257px;
    font-family: "Lora", serif; font-size: 12px; color: var(--ink-text);
  }
</style>
</head>
<body>
<main class="stage">
  <section class="card card--front" aria-label="Card front">
    <div class="front-brand">
      <span class="brand-mark"></span>
      <span class="brand-name">STATURE<br>CHIROPRACTIC</span>
    </div>
    <div class="front-web">
      <span class="dash"></span>
      <span>www.staturechiro.com</span>
      <span class="dash"></span>
    </div>
    <div class="front-stripe"><span class="blue"></span><span class="dark"></span></div>
  </section>

  <section class="card card--back" aria-label="Card back">
    <div class="back-brand">
      <span class="brand-mark"></span>
      <span class="brand-name">STATURE CHIROPRACTIC</span>
    </div>
    <div class="contact-band">
      <p class="person-name">Evan Hale Marsh</p>
      <p class="person-role">Managing Director</p>
      <ul class="contact-list">
        <li>
          <svg viewBox="0 0 12 12" aria-hidden="true"><path d="M1 4c0-2 2-3 5-3s5 1 5 3v1H8V4H4v1H1zM3 6h6l1.5 5h-9z"/></svg>
          <span>555-014-2270</span>
        </li>
        <li>
          <svg viewBox="0 0 12 12" aria-hidden="true"><path d="M0 2h12v1L6 7 0 3zM0 4.3l6 4 6-4V10H0z"/></svg>
          <span>evan@staturechiro.com</span>
        </li>
        <li>
          <svg viewBox="0 0 12 12" aria-hidden="true"><path d="M6 0a6 6 0 1 0 0 12A6 6 0 0 0 6 0zm0 1.2c.8.8 1.3 2.3 1.4 4.2H4.6C4.7 3.5 5.2 2 6 1.2zM1.3 6.6h2.2c.1 1.6.5 3 1.1 4A4.8 4.8 0 0 1 1.3 6.6zm0-1.2a4.8 4.8 0 0 1 3.3-4C4 2.4 3.6 3.8 3.5 5.4zm4.7 5.4c-.8-.8-1.3-2.3-1.4-4.2h2.8c-.1 1.9-.6 3.4-1.4 4.2zm1.4-.2c.6-1 1-2.4 1.1-4h2.2a4.8 4.8 0 0 1-3.3 4zm1.1-5.2c-.1-1.6-.5-3-1.1-4a4.8 4.8 0 0 1 3.3 4z"/></svg>
          <span>www.staturechiro.com</span>
        </li>
      </ul>
    </div>
    <p class="address">418 Larkmoor Rd., Fenwick, Eastvale, US 204817</p>
  </section>
</main>
</body>
</html>
```